Lanternfield Drinks business cards

We need a business card design for our new logo. The company is modern, progressive, professional, yet approachable. The key products are ready to drink bottles and cans of coffee based beverages.
These cards will be a critical part of the first impression made by our sales organization, business development team, and all external facing personnel.
Card can be a vertical or horizontal orientation.

Target Market(s)

Customers, suppliers, business partners

Industry/Entity Type

Business

Contact Information for Business Card

Business cards should feature Company Name and Logo.

Font styles to use
Serif

Colors

Designer to choose colors to be used in the design.

Requirements
Must have
• Strong readability of Name, phone #, mobile number and email address.
• Job title, website url, Street Address, and other details can be secondary level readability.
Nice to have
• High impact, simplistic quality design.
• Ok to utilize the 'H in the box' separate from the company name

```html
<!DOCTYPE html>
<html lang="en">
<head>
<meta charset="utf-8">
<title>Lanternfield Drinks business cards</title>
<link rel="stylesheet" href="https://fonts.googleapis.com/css2?family=Crimson+Pro:ital,wght@0,400;0,600;1,400&display=swap">
<style>
  :root {
    --backdrop: #3b3b3d;
    --card: #1d1d1f;
    --orange: #e4572e;
    --amber: #e99a2c;
    --ink: #f2f2f2;
    --muted: #c9c9c9;
  }
  * { margin: 0; padding: 0; box-sizing: border-box; }
  html, body { width: 799px; height: 1200px; overflow: hidden; }
  body {
    background: var(--backdrop);
    font-family: "Crimson Pro", Georgia, serif;
    position: relative;
  }
  .card {
    position: absolute;
    left: 60px;
    width: 680px;
    height: 389px;
    background: var(--card);
    border-radius: 6px;
    box-shadow: 0 12px 30px rgba(0,0,0,.45);
  }
  .card--front { top: 95px; }
  .card--back { top: 710px; }

  .brand {
    position: absolute;
    display: flex;
    align-items: center;
    gap: 16px;
    color: var(--orange);
    font-weight: 600;
    letter-spacing: 1px;
    white-space: nowrap;
  }
  .brand__square {
    border: 4px solid var(--orange);
    flex: none;
  }
  .brand-rule {
    position: absolute;
    height: 2px;
    background: var(--amber);
  }

  /* front */
  .card--front .brand {
    left: 0; right: 0; top: 120px;
    justify-content: center;
    font-size: 40px;
  }
  .card--front .brand__square { width: 56px; height: 56px; }
  .card--front .brand-rule { left: 150px; right: 150px; top: 196px; }
  .site-line {
    position: absolute;
    left: 0; right: 0; top: 268px;
    display: flex;
    align-items: center;
    justify-content: center;
    gap: 22px;
    font-size: 22px;
    color: var(--ink);
  }
  .site-line__dash {
    width: 60px; height: 4px;
    background: var(--orange);
    border-radius: 2px;
  }
  .site-line__domain { color: var(--orange); }

  /* back */
  .card--back .brand {
    left: 150px; top: 46px;
    font-size: 34px;
  }
  .card--back .brand__square { width: 52px; height: 52px; }
  .card--back .brand-rule { left: 230px; right: 60px; top: 116px; }
  .divider {
    position: absolute;
    left: 40px; right: 40px; top: 178px;
    height: 1px;
    background: var(--amber);
    opacity: .8;
  }
  .person {
    position: absolute;
    left: 0; right: 0; top: 196px;
    text-align: center;
  }
  .person__name {
    color: var(--orange);
    font-size: 32px;
    font-weight: 600;
  }
  .person__title {
    color: var(--ink);
    font-style: italic;
    font-size: 18px;
  }
  .contact {
    position: absolute;
    top: 290px;
    font-size: 19px;
    line-height: 1.45;
    color: var(--ink);
  }
  .contact--phones { left: 40px; }
  .contact--online { left: 235px; }
  .contact--address { left: 480px; }
  .contact__row { display: flex; align-items: center; gap: 10px; }
  .contact__row--top { align-items: flex-start; }
  .icon { width: 16px; height: 16px; flex: none; fill: var(--orange); }
</style>
</head>
<body>

<section class="card card--front">
  <div class="brand">
    <span class="brand__square"></span>
    <span class="brand__name">LANTERNFIELD DRINKS</span>
  </div>
  <div class="brand-rule"></div>
  <div class="site-line">
    <span class="site-line__dash"></span>
    <span>www.<span class="site-line__domain">lanternfielddrinks</span>.com</span>
    <span class="site-line__dash"></span>
  </div>
</section>

<section class="card card--back">
  <div class="brand">
    <span class="brand__square"></span>
    <span class="brand__name">LANTERNFIELD DRINKS</span>
  </div>
  <div class="brand-rule"></div>
  <div class="divider"></div>

  <div class="person">
    <div class="person__name">John Doe Smith</div>
    <div class="person__title">Managing Director</div>
  </div>

  <div class="contact contact--phones">
    <div class="contact__row">
      <svg class="icon" viewBox="0 0 16 16" aria-hidden="true"><path d="M2 5c0-2 1-3 6-3s6 1 6 3v1h-3V4.5H5V6H2zM4 7h8l2 7H2z"/></svg>
      <span>555.555.5555</span>
    </div>
    <div class="contact__row">
      <svg class="icon" viewBox="0 0 16 16" aria-hidden="true"><path d="M4 1h8a1 1 0 0 1 1 1v12a1 1 0 0 1-1 1H4a1 1 0 0 1-1-1V2a1 1 0 0 1 1-1zm1 2v9h6V3z"/></svg>
      <span>666.666.7777</span>
    </div>
  </div>

  <div class="contact contact--online">
    <div class="contact__row">
      <svg class="icon" viewBox="0 0 16 16" aria-hidden="true"><path d="M1 3h14v10H1zm1.5 1.2L8 8.5l5.5-4.3z"/></svg>
      <span>johndoe@yourwebsite.com</span>
    </div>
    <div class="contact__row">
      <svg class="icon" viewBox="0 0 16 16" aria-hidden="true"><path d="M8 1a7 7 0 1 0 0 14A7 7 0 0 0 8 1zm-1 2.2V7H3.1A5 5 0 0 1 7 3.2zm2 0A5 5 0 0 1 12.9 7H9zM3.1 9H7v3.8A5 5 0 0 1 3.1 9zM9 9h3.9A5 5 0 0 1 9 12.8z"/></svg>
      <span>www.yourwebsite.com</span>
    </div>
  </div>

  <div class="contact contact--address">
    <div class="contact__row contact__row--top">
      <svg class="icon" viewBox="0 0 16 16" aria-hidden="true" style="margin-top:5px"><path d="M8 0a5 5 0 0 0-5 5c0 4 5 11 5 11s5-7 5-11a5 5 0 0 0-5-5zm0 7a2 2 0 1 1 0-4 2 2 0 0 1 0 4z"/></svg>
      <span>234 Anywhere St.,<br>Any Town, US 1234</span>
    </div>
  </div>
</section>

</body>
</html>
```